4th Generation Family Business Needs a New Card Design!

We are a family owned 4th Generation company. We are based in the Sydney, Australia area and we are desperately in need of a more modern and classy card. We are monumental masons who design, supply & erect lasting memorials throughout cemeteries in Sydney. Our customers are normally in a period of grieving. I have attached logo files that will need to be implemented on the card. Company was established 1935. Australian Owned and Operated. Card needs to be designed to PIXO.com specification.

Target Market(s)

Our target market is based upon people that a grieving for family members that have passed away. We also deal with alot of companies that own and operate cemeteries.

Industry/Entity Type

Business

Contact Information for Business Card

Simon Harcourt, Operations Manager, 0417293086, simon@harcourtmemorials.com.au
Lewis Harcourt, Director, 0491630572, lewis@harcourtmemorials.com.au
Phone # 02 9561 3048
Website: www.harcourtmemorials.com.au
Address: Suite 17, 8 Palfrey Lane, West Carlow, Sydney NSW 2156

Font styles to use
Serif
Decorative
Script

Requirements
Must have
• Would like to see the logo nicely implemented with a modern design. Embossed lettering would be a nice additive.

```html
<!DOCTYPE html>
<html lang="en">
<head>
<meta charset="utf-8">
<title>Harcourt Memorials — Business Card</title>
<link href="https://fonts.googleapis.com/css2?family=Cinzel:wght@400;600&family=Open+Sans:wght@400&display=swap" rel="stylesheet">
<style>
  :root {
    --backdrop: #2b2522;
    --card: #1c1e21;
    --card-edge: #141517;
    --gold: #e0a920;
    --white: #f2f2f2;
    --muted: #c9c9c9;
    --divider: #4a4c50;
    --emboss: #8d9094;
  }
  html, body {
    margin: 0;
    width: 1200px;
    height: 769px;
    overflow: hidden;
    background: var(--backdrop);
  }
  .canvas {
    position: relative;
    width: 1200px;
    height: 769px;
  }
  .card {
    position: absolute;
    top: 226px;
    width: 520px;
    height: 318px;
    background: var(--card);
    box-shadow: 0 0 0 1px var(--card-edge);
    border-radius: 3px;
    overflow: hidden;
  }
  .card--front { left: 60px; }
  .card--back { left: 620px; }

  .brand {
    position: absolute;
    display: flex;
    flex-direction: column;
    align-items: center;
    font-family: "Cinzel", serif;
    font-weight: 400;
    text-align: center;
  }
  .brand__mark {
    width: 46px;
    height: 46px;
    border: 3px solid currentColor;
    box-sizing: border-box;
    margin-bottom: 14px;
  }
  .brand__name {
    font-size: 27px;
    line-height: 1;
    letter-spacing: 1px;
  }
  .brand__sub {
    font-size: 15px;
    letter-spacing: 3px;
    margin-top: 6px;
  }
  .card--front .brand {
    left: 20px;
    top: 92px;
    width: 220px;
    color: var(--white);
  }
  .card--back .brand {
    left: 0;
    right: 0;
    top: 96px;
    color: var(--emboss);
  }
  .card--back .brand__name { font-size: 32px; }
  .card--back .brand__mark { width: 54px; height: 54px; }

  .divider {
    position: absolute;
    left: 258px;
    top: 40px;
    width: 1px;
    height: 238px;
    background: var(--divider);
  }

  .contact {
    position: absolute;
    left: 282px;
    top: 58px;
    width: 230px;
    font-family: "Open Sans", sans-serif;
    color: var(--white);
  }
  .contact__name {
    font-family: "Cinzel", serif;
    font-weight: 600;
    font-size: 16px;
    color: var(--gold);
    margin: 0;
    letter-spacing: .5px;
  }
  .contact__role {
    font-family: "Cinzel", serif;
    font-size: 12px;
    color: var(--muted);
    margin: 3px 0 10px;
    letter-spacing: .5px;
  }
  .contact__address {
    font-size: 11px;
    line-height: 16px;
    font-style: normal;
    margin-bottom: 8px;
  }
  .contact__list {
    list-style: none;
    margin: 0;
    padding: 0;
    font-size: 11px;
    line-height: 18px;
  }
  .contact__list li {
    display: flex;
    align-items: center;
    gap: 7px;
    white-space: nowrap;
  }
  .icon {
    width: 10px;
    height: 10px;
    flex: none;
    fill: var(--gold);
  }
</style>
</head>
<body>
<main class="canvas">

  <section class="card card--front" aria-label="Business card front">
    <div class="brand">
      <span class="brand__mark"></span>
      <span class="brand__name">Harcourt</span>
      <span class="brand__sub">Memorials</span>
    </div>

    <div class="divider"></div>

    <div class="contact">
      <h1 class="contact__name">Simon Harcourt</h1>
      <p class="contact__role">Operations Manager</p>
      <address class="contact__address">
        Suite 17, 8 Palfrey Lane<br>
        West Carlow, Sydney NSW 2156
      </address>
      <ul class="contact__list">
        <li>
          <svg class="icon" viewBox="0 0 10 10"><path d="M2 0.5 L3.6 2.6 L2.8 3.6 Q4 6 6.4 7.2 L7.4 6.4 L9.5 8 L8.4 9.5 Q2.5 9 0.5 1.6 Z"/></svg>
          02 9561 3048
        </li>
        <li>
          <svg class="icon" viewBox="0 0 10 10"><path d="M2.5 0 H7.5 V10 H2.5 Z M3.4 1 V8 H6.6 V1 Z"/></svg>
          0417293086
        </li>
        <li>
          <svg class="icon" viewBox="0 0 10 10"><path d="M0 2 H10 V8.5 H0 Z M0.8 2.6 L5 5.6 L9.2 2.6 Z"/></svg>
          simon@harcourtmemorials.com.au
        </li>
        <li>
          <svg class="icon" viewBox="0 0 10 10"><circle cx="5" cy="5" r="5"/></svg>
          www.harcourtmemorials.com.au
        </li>
      </ul>
    </div>
  </section>

  <section class="card card--back" aria-label="Business card back">
    <div class="brand">
      <span class="brand__mark"></span>
      <span class="brand__name">Harcourt</span>
      <span class="brand__sub">Memorials</span>
    </div>
  </section>

</main>
</body>
</html>
```